Belmont Ridge Business Card Design Project

We have recently rebranded and would like to design new business cards that incorporate the corporate logo - double sided cards with corporate logo on one side and contact details on the other

Target Market(s)

Sophisticated and high net worth investors and finance industry professionals

Industry/Entity Type

Funds Management

Contact Information for Business Card

The card should prominently feature the company name and logo. Other details will be standard contact details for each staff member - name, address, phone, email, website

Colors
0054AA
0677BA
7BADD7
CADEEF
E8F1F8

Requirements
Must have
• Double-sided design with one side prominently featuring the corporate logo and the other side with all standard contact details

```html
<!DOCTYPE html>
<html lang="en">
<head>
<meta charset="utf-8">
<title>Belmont Ridge – Business Card</title>
<link rel="stylesheet" href="https://fonts.googleapis.com/css2?family=Open+Sans:wght@400;600;700&display=swap">
<style>
  :root {
    --backdrop: #ababab;
    --card-dark: #0c1118;
    --card-dark-edge: #1a1f27;
    --card-light: #ffffff;
    --accent-blue: #6798c8;
    --deep-blue: #1f3d66;
    --ink: #111111;
    --body-grey: #5a5a5a;
    --logo-white: #ffffff;
  }
  * { box-sizing: border-box; margin: 0; padding: 0; }
  html, body {
    width: 1200px;
    height: 1000px;
    overflow: hidden;
  }
  body {
    position: relative;
    background: var(--backdrop);
    font-family: "Open Sans", Arial, sans-serif;
  }
  .card {
    position: absolute;
    width: 514px;
    height: 297px;
  }
  .card--front {
    left: 57px;
    top: 339px;
    background: var(--card-dark);
    overflow: hidden;
  }
  .card--front .pattern-area {
    position: absolute;
    inset: 0;
    background: linear-gradient(180deg, var(--card-dark-edge) 0%, var(--card-dark) 50%, var(--card-dark-edge) 100%);
  }
  .brand {
    position: absolute;
    left: 62px;
    top: 132px;
    display: flex;
    align-items: center;
    gap: 16px;
  }
  .brand__mark {
    width: 18px;
    height: 18px;
    border-radius: 50%;
    background: var(--logo-white);
  }
  .brand__name {
    color: var(--logo-white);
    font-size: 34px;
    font-weight: 600;
    letter-spacing: 1px;
    line-height: 1;
  }
  .card--back {
    left: 614px;
    top: 338px;
    background: var(--card-light);
  }
  .contact {
    position: absolute;
    left: 45px;
    top: 71px;
    font-size: 14px;
    line-height: 17px;
    color: var(--body-grey);
  }
  .contact__name {
    color: var(--accent-blue);
    font-weight: 700;
    letter-spacing: 1.4px;
    text-transform: uppercase;
  }
  .contact__role {
    color: var(--ink);
    font-weight: 700;
    letter-spacing: 1.4px;
    text-transform: uppercase;
  }
  .contact__group { margin-top: 16px; }
  .contact__web {
    margin-top: 17px;
    color: var(--deep-blue);
    font-weight: 700;
    letter-spacing: 0.5px;
  }
</style>
</head>
<body>
  <section class="card card--front">
    <div class="pattern-area" role="img" aria-label="Dark repeating sail-shape background pattern"></div>
    <div class="brand">
      <span class="brand__mark"></span>
      <span class="brand__name">Belmont Ridge</span>
    </div>
  </section>

  <section class="card card--back">
    <div class="contact">
      <p class="contact__name">Daniel Harcourt</p>
      <p class="contact__role">Portfolio Manager</p>
      <div class="contact__group">
        <p>+02 9000 4417</p>
        <p>dharcourt@belmontridge.com</p>
      </div>
      <div class="contact__group">
        <p>Level 14 Harbourview House,</p>
        <p>52 Kellman Street,</p>
        <p>Sydney NSW 2000</p>
      </div>
      <p class="contact__web">www.belmontridge.com</p>
    </div>
  </section>
</body>
</html>
```